Hong Kong based International Remittance and ForEx company requires website design

We need a website designed for a new European - Hong Kong based ForEx & fund remittence entity.

The company specialises in larger corporate & high net worth private client trades, therefore the design must aesthetically reflect this (sophisticated). As a theme colour, financial entities tend to use either blue or red; if blue, our preference is a darker blue. Visually, our preference is less copy, more imagery.

Number of pages would be limited; landing (home), about us, client registration (x1 Corporate form, x1 Private Client form), Contact Us.

Have uploaded the existing logo - please note this is to be redesigned, although the colour scheme will remain the same. Please also note that copy will follow - please use Lorem Ipsum.

Target Market(s)

Medium to large Corporations. High net worth individuals.

Industry/Entity Type

Financial Service

Coding

Coded - Design and coding required

Number of Pages Required

4 page

Font styles to use
Serif

Requirements
Nice to have
• ForEx ticker,

```html
<!DOCTYPE html>
<html lang="en">
<head>
<meta charset="utf-8">
<title>Harbourline Incorporation – International Payment Services</title>
<link href="https://fonts.googleapis.com/css2?family=Roboto:wght@300;400;500;700&display=swap" rel="stylesheet">
<style>
:root{
  --blue:#1a6fc0;
  --blue-dark:#0f5aa6;
  --blue-footer:#1668b8;
  --link:#1b75c9;
  --ink:#222;
  --body:#555;
  --line:#dcdcdc;
  --up:#1f9a2e;
  --down:#d32222;
  --ticker-bg:#efefef;
  --black:#111;
}
*{box-sizing:border-box;margin:0;padding:0}
html,body{width:1200px;height:2230px;overflow:hidden}
body{position:relative;background:#fff;font-family:"Roboto",Arial,sans-serif;color:var(--ink)}
.abs{position:absolute}

/* header */
.site-header{left:0;top:0;width:1200px;height:138px;background:linear-gradient(#fff,#f1f1f1);box-shadow:0 2px 4px rgba(0,0,0,.12)}
.brand{left:89px;top:42px;display:flex;flex-direction:column;gap:4px}
.brand-name{font-size:36px;font-weight:400;color:#25355e;line-height:1}
.brand-sub{font-size:9px;letter-spacing:2.6px;color:#25355e;font-weight:400}
.lang{right:88px;top:28px;font-size:13px;color:#333}
.lang .active{color:var(--link)}
.lang span.sep{margin:0 6px;color:#888}
.main-nav{right:150px;top:81px;display:flex;gap:25px;font-size:14px;color:#333;white-space:nowrap}
.main-nav .active{color:var(--link)}
.nav-divider{left:1076px;top:74px;width:1px;height:30px;background:#777}
.search-icon{left:1096px;top:80px}

/* hero */
.hero{left:0;top:138px;width:1200px;height:551px;background:linear-gradient(135deg,#cfd8e2 0%,#e9eef3 35%,#9fb3c7 60%,#d9e2ea 100%)}
.hero-caption{left:86px;top:525px;min-width:512px;height:131px;background:rgba(26,111,192,.85);padding:22px 22px;white-space:nowrap}
.hero-caption h1{font-size:31px;font-weight:400;color:#fff;line-height:42px}
.hero-caption p{font-size:31px;font-weight:400;color:#fff;line-height:42px}
.slider-arrows{left:1047px;top:614px;display:flex;gap:2px}
.slider-arrows span{width:30px;height:41px;background:rgba(40,40,40,.75);display:flex;align-items:center;justify-content:center}

/* ticker */
.ticker{left:0;top:689px;width:1200px;height:50px;background:var(--ticker-bg);display:flex;align-items:center;padding-left:98px;gap:41px;font-size:13px;font-weight:700;color:var(--blue);white-space:nowrap}
.ticker .up{color:var(--up)}
.ticker .down{color:var(--down)}

/* welcome */
.welcome{left:88px;top:793px;width:622px}
.section-title{font-size:23px;font-weight:400;color:var(--ink);text-transform:uppercase;white-space:nowrap}
.section-title em{font-style:normal;color:var(--blue)}
.welcome p{font-size:11px;line-height:21px;color:var(--body);text-align:justify;margin-top:9px}
.btn{display:inline-block;background:var(--blue-dark);color:#fff;font-size:10px;font-weight:500;padding:8px 14px;border-radius:2px}
.converter{left:739px;top:793px;width:376px;height:220px;background:linear-gradient(135deg,#1e7ad0,#1460ae);border:2px solid #0d4f96;padding:33px 26px}
.converter .row{display:flex;gap:10px;margin-bottom:12px}
.field{height:37px;background:#fff;font-size:14px;color:#333;display:flex;align-items:center;padding:0 10px}
.field.amount{width:108px}
.field.currency{width:204px;justify-content:space-between}
.converter .result{color:#fff;font-size:14px;line-height:27px;margin-top:14px;padding-left:4px}

/* expertise */
.expertise{left:0;top:1060px;width:1200px;height:409px;background:linear-gradient(120deg,#1b2735 0%,#3a2520 40%,#2a3342 70%,#142031 100%)}
.expertise h2{position:absolute;top:50px;width:100%;text-align:center;color:#fff;font-size:27px;font-weight:400}
.service{position:absolute;top:123px;width:330px;text-align:center;color:#fff}
.service .badge{width:116px;height:116px;border-radius:50%;background:var(--blue);border:5px solid #fff;margin:0 auto;display:flex;align-items:center;justify-content:center}
.service h3{font-size:16px;font-weight:400;margin-top:20px;text-transform:uppercase;white-space:nowrap}
.service p{font-size:11.5px;line-height:19px;color:#ddd;margin:14px auto 0;width:270px}

/* about & blog */
.about{left:90px;top:1515px;width:490px}
.about-photo{width:491px;height:245px;margin-top:14px;border:3px solid #e3e3e3;background:linear-gradient(135deg,#f4f4f4 0%,#bdbdbd 45%,#e2c2a4 60%,#3c3c3c 100%)}
.about p{font-size:11.5px;line-height:20px;color:var(--body);margin-top:9px;text-align:justify}
.more{font-size:12px;color:var(--link);margin-top:4px;display:block}
.blog{left:626px;top:1515px;width:489px}
.blog-arrows{right:0;top:0}
.post{position:absolute;left:0;width:489px;height:156px;border-bottom:1px solid var(--line)}
.post-thumb{position:absolute;left:0;top:0;width:184px;height:122px}
.post-body{position:absolute;left:200px;top:4px;width:289px}
.post-body h4{font-size:14px;font-weight:400;color:var(--ink)}
.post-body .date{font-size:10px;color:var(--link);margin-top:6px}
.post-body p{font-size:11px;line-height:17px;color:var(--body);text-align:justify;margin-top:3px}
.post-body .more{font-size:11px;margin-top:6px}

/* footer */
.site-footer{left:0;top:1923px;width:1200px;height:238px;background:var(--blue-footer);color:#fff}
.fcol{position:absolute;top:50px}
.fcol h5{font-size:15px;font-weight:500;text-transform:uppercase}
.fcol p,.fcol li{font-size:12px;line-height:17px}
.signup-input{width:215px;height:30px;background:#eee;border:1px solid #ccc;color:#666;font-size:11px;padding:8px 10px;margin-top:14px}
.signup-btn{display:inline-block;margin-top:10px;background:#eee;color:#222;font-size:12px;font-weight:500;padding:7px 11px;border-radius:3px}
.contact li{list-style:none;margin-top:14px}
.social li{list-style:none;display:flex;align-items:center;gap:14px;margin-top:11px}
.social .dot{width:33px;height:33px;border-radius:50%;border:1.5px solid #fff}
.copyright{left:0;top:2161px;width:1200px;height:69px;background:var(--black);color:#fff;font-size:12px;text-align:center;line-height:48px}
</style>
</head>
<body>

<header class="abs site-header">
  <div class="abs brand"><span class="brand-name">Harbourline</span><span class="brand-sub">INCORPORATION LIMITED</span></div>
  <div class="abs lang"><span class="active">ENGLISH</span><span class="sep">|</span>CANTONESE<span class="sep">|</span>RUSSIAN</div>
  <nav class="abs main-nav"><span class="active">HOME</span><span>ABOUT US</span><span>INTERNATIONAL PAYMENTS</span><span>CLIENT APPLICATION</span><span>CONTACT US</span></nav>
  <div class="abs nav-divider"></div>
  <svg class="abs search-icon" width="16" height="16" viewBox="0 0 16 16"><circle cx="6.5" cy="6.5" r="5" fill="none" stroke="#222" stroke-width="2"/><line x1="10" y1="10" x2="15" y2="15" stroke="#222" stroke-width="2.4"/></svg>
</header>

<section class="abs hero" role="img" aria-label="Business person pointing at a bar chart on a tablet beside a coffee cup and a glass of water"></section>
<div class="abs hero-caption"><h1>HARBOURLINE INCORPORATION</h1><p>International payment services</p></div>
<div class="abs slider-arrows">
  <span><svg width="10" height="18" viewBox="0 0 10 18"><polyline points="8,1 2,9 8,17" fill="none" stroke="#fff" stroke-width="1.6"/></svg></span>
  <span><svg width="10" height="18" viewBox="0 0 10 18"><polyline points="2,1 8,9 2,17" fill="none" stroke="#fff" stroke-width="1.6"/></svg></span>
</div>

<div class="abs ticker">
  <span>GBP/CAD = <b class="up">1.87827 ▲</b></span>
  <span>GBP/USD = <b class="down">1.38508 ▼</b></span>
  <span>GBP/NZD = <b class="down">2.09647 ▼</b></span>
  <span>GBP/TRY = <b class="down">4.1037 ▼</b></span>
  <span>GBP/DKK = <b class="up">9.47968 ▲</b></span>
  <span>GBP/AED = <b class="down">5.08324 ▼</b></span>
</div>

<section class="abs welcome">
  <h2 class="section-title">Welcome to <em>Harbourline Incorporation</em></h2>
  <p>Lorem Ipsum has been the industry's standard dummy text ever since the 1500s, when an unknown printer took a galley of type and scrambled it to make a type specimen book. It has survived not only five centuries, but also the leap into electronic typesetting, remaining essentially unchanged. It was popularised in the 1960s with the release of Letraset sheets containing Lorem Ipsum passages, and more recently with desktop publishing software.</p>
  <p>It has survived not only five centuries, but also the leap into electronic typesetting, remaining essentially unchanged. It was popularised in the 1960s with the release of Letraset sheets containing Lorem Ipsum passages, and more recently</p>
  <span class="btn" style="margin-top:16px">READ MORE</span>
</section>

<aside class="abs converter">
  <div class="row"><div class="field amount">100</div><div class="field currency">British Pound Sterling <span>▾</span></div></div>
  <div class="row"><div class="field amount">1077.95</div><div class="field currency">Hong Kong Dollar <span>▾</span></div></div>
  <div class="result">100.00 British Pound Sterling is<br>1,078.180 Hong Kong Dollar</div>
</aside>

<section class="abs expertise" role="img" aria-label="Dark background of glowing financial charts and data lines">
  <h2>EXPERTISE</h2>
  <div class="service" style="left:83px">
    <div class="badge"><svg width="48" height="34" viewBox="0 0 48 34"><rect x="2" y="2" width="44" height="30" rx="2" fill="none" stroke="#fff" stroke-width="3"/><rect x="8" y="8" width="32" height="18" fill="#fff"/><circle cx="24" cy="17" r="6" fill="var(--blue)"/></svg></div>
    <h3>International Money Transfer</h3>
    <p>Lorem ipsum dolor sit amet, consectetur adipising elit, sed do eiusmod tempor iunt ut labore et dolore magna aliqua. eiusmod</p>
  </div>
  <div class="service" style="left:442px">
    <div class="badge"><svg width="40" height="30" viewBox="0 0 40 30"><path d="M4 9h28M26 3l7 6-7 6M36 21H8M14 15l-7 6 7 6" fill="none" stroke="#fff" stroke-width="3.5"/></svg></div>
    <h3>Foreign Exchange</h3>
    <p>Lorem ipsum dolor sit amet, consectetur adipising elit, sed do eiusmod tempor iunt ut labore et dolore magna aliqua. eiusmod</p>
  </div>
  <div class="service" style="left:803px">
    <div class="badge"><svg width="44" height="40" viewBox="0 0 44 40"><rect x="2" y="2" width="40" height="28" rx="2" fill="#fff"/><rect x="18" y="30" width="8" height="5" fill="#fff"/><rect x="12" y="35" width="20" height="3" fill="#fff"/></svg></div>
    <h3>Paying &amp; Receiving Agency</h3>
    <p>Lorem ipsum dolor sit amet, consectetur adipising elit, sed do eiusmod tempor iunt ut labore et dolore magna aliqua. eiusmod</p>
  </div>
</section>

<section class="abs about">
  <h2 class="section-title" style="font-size:19px">About Us</h2>
  <div class="about-photo" role="img" aria-label="Two business people shaking hands"></div>
  <p>Harbourline is a leading provider of international payment services and foreign exchange to corporations and individuals covering most of the world including; throughout Asia, South America, and Europe. We engage with our clients with unmatched personalised service</p>
  <span class="more">Read More »</span>
</section>

<section class="abs blog">
  <h2 class="section-title" style="font-size:19px">Latest <em>Blog</em></h2>
  <svg class="abs blog-arrows" width="24" height="14" viewBox="0 0 24 14" style="top:5px"><polyline points="8,1 2,7 8,13" fill="none" stroke="#222" stroke-width="2"/><polyline points="16,1 22,7 16,13" fill="none" stroke="#222" stroke-width="2"/></svg>
  <article class="post" style="top:39px">
    <div class="post-thumb" role="img" aria-label="Calculator and pen on a desk" style="background:linear-gradient(135deg,#2f5f9a,#a9c3de 60%,#e8eef5)"></div>
    <div class="post-body"><h4>Nemo Enim Ipsam Volup</h4><div class="date">09-07-2016</div><p>Lorem Ipsum has been the industry's standard dummy text ever since the 1500s, when an unknown printer took a galley of type and scrambled</p><span class="more">Read More »</span></div>
  </article>
  <article class="post" style="top:211px">
    <div class="post-thumb" role="img" aria-label="Close-up of a payment card" style="background:linear-gradient(135deg,#222,#4a4a4a 50%,#9aa6b5)"></div>
    <div class="post-body"><h4>Nemo Enim Ipsam Volup</h4><div class="date">09-07-2016</div><p>Lorem Ipsum has been the industry's standard dummy text ever since the 1500s, when an unknown printer took a galley of type and scrambled</p><span class="more">Read More »</span></div>
  </article>
</section>

<footer class="abs site-footer">
  <div class="fcol" style="left:117px;width:240px">
    <h5>Newsletters Sign Up</h5>
    <p style="margin-top:14px">Sign up for our daily email by entering your information below</p>
    <div class="signup-input">Email address</div>
    <span class="signup-btn">SUBSCRIBE</span>
  </div>
  <div class="fcol" style="left:421px;width:240px">
    <h5>Latest Tweet</h5>
    <p style="margin-top:18px;display:flex;gap:8px"><svg width="20" height="16" viewBox="0 0 20 16"><path d="M2 3l7 5 7-5" fill="none" stroke="#fff" stroke-width="2"/><rect x="1" y="1" width="18" height="14" rx="2" fill="none" stroke="#fff" stroke-width="1.6"/></svg>Featured Workspace : Bluemill</p>
    <p style="margin:6px 0 0 28px;font-style:italic">bmill.to/8Xr2pQ"</p>
    <p style="margin:10px 0 0 28px">10 hours ago</p>
  </div>
  <ul class="fcol contact" style="left:711px;width:260px">
    <h5>Get In Touch</h5>
    <li>Phone : (852) 2100 4500</li>
    <li>Tel: 020 7000 1234</li>
    <li>Phone : (856) 2900 3100</li>
    <li>Email : info@harbourlinecorp.com</li>
  </ul>
  <ul class="fcol social" style="left:990px">
    <h5>Follow Us On</h5>
    <li style="margin-top:18px"><span class="dot"></span>Linkface</li>
    <li><span class="dot"></span>Chirper</li>
    <li><span class="dot"></span>Snapgram</li>
  </ul>
</footer>
<div class="abs copyright">Copyright © 2016. All Rights Reserved</div>

</body>
</html>
```